Real Estate Card Design

I need a new business card! Below you will find my headshot, the company logo and a copy of my previous business card.

The card must contain the following information:

Dana Wexley
Sales Representative
FERNBROOK HOMES REALTY INC BROKERGE
204-517 Marsh Rd E, Oshawa ON L1H 4K7
Cell: 905-618-3074 Office:905-481-2696
www.danawexley.example dana@homesbywexley.example

I would like the card to portray security and class all the while being fresh and contemporary. I hold the key....

```html
<!DOCTYPE html>
<html lang="en">
<head>
<meta charset="utf-8">
<title>Dana Wexley – Business Card</title>
<link rel="stylesheet" href="https://fonts.googleapis.com/css2?family=Libre+Baskerville&family=Open+Sans:wght@400;600&display=swap">
<style>
  :root {
    --backdrop: #3b3c3e;
    --card: #050a09;
    --accent: #0ea3e4;
    --text: #f4f6f7;
    --photo-dark: #0b0f10;
    --photo-warm: #6b5a4c;
  }
  * { box-sizing: border-box; margin: 0; padding: 0; }
  html, body {
    width: 1200px; height: 896px; overflow: hidden;
    background: var(--backdrop);
  }
  .sheet {
    width: 1200px; height: 896px;
    display: flex; flex-direction: column; align-items: center; justify-content: center;
    gap: 40px;
  }
  .card {
    position: relative;
    width: 700px; height: 400px;
    background: var(--card);
    overflow: hidden;
    box-shadow: 0 14px 30px rgba(0,0,0,.45);
  }
  .card__band {
    position: absolute; left: 0; right: 0; bottom: 0;
    height: 14px; background: var(--accent);
  }
  /* Front */
  .front__details {
    position: absolute; left: 46px; top: 62px;
    font-family: "Open Sans", sans-serif; color: var(--text);
  }
  .agent-name {
    font-family: "Libre Baskerville", serif;
    font-size: 34px; letter-spacing: 1px;
    color: var(--accent); font-weight: 400;
    text-transform: uppercase;
  }
  .agent-title { font-size: 19px; margin: 2px 0 14px; }
  .contact-list { list-style: none; font-size: 18px; line-height: 27px; }
  .contact-list li { display: flex; align-items: center; gap: 10px; }
  .contact-list svg { width: 16px; height: 16px; flex: none; }
  .brokerage {
    margin-top: 6px; font-size: 18px; line-height: 25px;
    color: var(--accent); text-transform: uppercase;
  }
  .address { font-size: 18px; line-height: 25px; }
  .front__photo {
    position: absolute; right: 0; top: 0; bottom: 14px; width: 300px;
    background: radial-gradient(ellipse at 55% 55%, var(--photo-warm) 0%, #2a2a2c 50%, var(--photo-dark) 85%);
  }
  /* Back */
  .back__brand {
    position: absolute; left: 0; right: 0; top: 110px;
    display: flex; align-items: center; justify-content: center; gap: 22px;
  }
  .brand-mark { width: 86px; height: 86px; background: var(--accent); }
  .brand-name {
    font-family: "Libre Baskerville", serif; font-size: 30px;
    line-height: 38px; color: var(--text); text-transform: uppercase;
    letter-spacing: 1px;
  }
  .back__url {
    position: absolute; left: 0; right: 0; top: 262px; text-align: center;
    font-family: "Open Sans", sans-serif; font-size: 22px; color: var(--accent);
  }
</style>
</head>
<body>
<main class="sheet">
  <section class="card card--front" aria-label="Card front">
    <div class="front__details">
      <h1 class="agent-name">Dana Wexley</h1>
      <p class="agent-title">Sales Representative</p>
      <ul class="contact-list">
        <li>
          <svg viewBox="0 0 16 16" aria-hidden="true"><rect x="4" y="1" width="8" height="14" rx="1.5" fill="none" stroke="#f4f6f7" stroke-width="1.6"/><circle cx="8" cy="12.5" r="0.9" fill="#f4f6f7"/></svg>
          905-618-3074
        </li>
        <li>
          <svg viewBox="0 0 16 16" aria-hidden="true"><path d="M2 6c0-2 2.5-3 6-3s6 1 6 3v1.5h-3V6H5v1.5H2z" fill="#f4f6f7"/><rect x="4" y="8" width="8" height="6" rx="1" fill="#f4f6f7"/></svg>
          905-481-2696
        </li>
        <li>
          <svg viewBox="0 0 16 16" aria-hidden="true"><rect x="1" y="3" width="14" height="10" rx="1" fill="#f4f6f7"/><path d="M1.5 3.5 8 9l6.5-5.5" fill="none" stroke="#050a09" stroke-width="1.3"/></svg>
          dana@homesbywexley.example
        </li>
        <li>
          <svg viewBox="0 0 16 16" aria-hidden="true"><circle cx="8" cy="8" r="7" fill="#f4f6f7"/><path d="M1 8h14M8 1c-3 3-3 11 0 14M8 1c3 3 3 11 0 14" fill="none" stroke="#050a09" stroke-width="1"/></svg>
          www.danawexley.example
        </li>
      </ul>
      <p class="brokerage">Fernbrook Homes<br>Realty Inc Brokerge</p>
      <p class="address">204-517 Marsh Rd E, Oshawa<br>ON L1H 4K7</p>
    </div>
    <div class="front__photo" role="img" aria-label="Portrait of the agent holding a house key"></div>
    <div class="card__band"></div>
  </section>

  <section class="card card--back" aria-label="Card back">
    <div class="back__brand">
      <span class="brand-mark" aria-hidden="true"></span>
      <p class="brand-name">Fernbrook Homes<br>Realty Inc.</p>
    </div>
    <p class="back__url">www.danawexley.example</p>
    <div class="card__band"></div>
  </section>
</main>
</body>
</html>
```